Timber Crest Construction Needs business card

Hey we are in need of business card designs. I have upload our logo as a guideline, but free feel to run with it or come up with something unique.
Pls have fun with it and be creative. the name says it all!
i will give some directions after i see a few entries..
Updates
Logo source file has been uploaded..
Hey because of the logo is so colourful already.
Can we have a few submissions with less colour.
Also we are looking for clever/hidden/descriptive business card.

```html
<!DOCTYPE html>
<html lang="en">
<head>
<meta charset="utf-8">
<title>Timber Crest Construction – Business Card</title>
<link href="https://fonts.googleapis.com/css2?family=Cinzel:wght@600&display=swap" rel="stylesheet">
<style>
  :root {
    --page: #ececec;
    --card-white: #ffffff;
    --card-black: #000000;
    --slate: #6f7f86;
    --text-light: #ffffff;
  }
  html, body {
    margin: 0;
    padding: 0;
    width: 1200px;
    height: 1186px;
    overflow: hidden;
    background: var(--page);
  }
  .canvas {
    position: relative;
    width: 1200px;
    height: 1186px;
  }
  .card {
    position: absolute;
    left: 220px;
    width: 760px;
    height: 440px;
    box-shadow: 0 0 0 1px #cfcfcf;
    overflow: hidden;
  }
  .card-front { top: 90px; }
  .card-back { top: 640px; }

  .front-brand {
    height: 235px;
    background: var(--card-white);
    display: flex;
    align-items: center;
    justify-content: center;
  }
  .brand-name {
    font-family: "Cinzel", serif;
    font-weight: 600;
    font-size: 40px;
    letter-spacing: 1px;
    color: var(--slate);
    margin: 0;
  }
  .front-contact {
    height: 205px;
    background: var(--card-black);
    color: var(--text-light);
    font-family: "Cinzel", serif;
    font-weight: 600;
    font-size: 26px;
    letter-spacing: 3px;
    text-align: center;
    display: flex;
    flex-direction: column;
    justify-content: center;
    line-height: 37px;
  }
  .front-contact p { margin: 0; }

  .back-pattern {
    display: block;
    width: 760px;
    height: 440px;
  }
</style>
</head>
<body>
<main class="canvas">
  <section class="card card-front">
    <div class="front-brand">
      <h1 class="brand-name">Timber Crest Construction</h1>
    </div>
    <div class="front-contact">
      <p class="contact-name">Proprietor Name</p>
      <p class="contact-phone">000000000</p>
      <p class="contact-email">Email</p>
      <p class="contact-address">Address</p>
    </div>
  </section>

  <section class="card card-back">
    <svg class="back-pattern" viewBox="0 0 760 440" role="img" aria-label="Checkered block pattern in grey, black and white covering the card back">
      <defs>
        <linearGradient id="backTone" x1="0" y1="0" x2="1" y2="1">
          <stop offset="0" stop-color="#6f7f86"/>
          <stop offset="0.5" stop-color="#3a3f42"/>
          <stop offset="1" stop-color="#8a9499"/>
        </linearGradient>
      </defs>
      <rect width="760" height="440" fill="url(#backTone)"/>
    </svg>
  </section>
</main>
</body>
</html>
```